Fitness Equipment & Service

I want to make the card eye catching and fun. We are called Corvane Motion Limited and we are based in Wales. We sell, install and service all types of fitness equipment from Skipping ropes, right through the Dumbbells, Kettle bells and Barbells through to state of the art Treadmills, Running Machines and Strength Equipment. We also design and install changing room furniture and lockers.

TYPOGRAPHY
We would like to use Futrura. Futura has an appearance of efficiency and forwardness. The typeface is derived
from simple geometric forms (near-perfect circles, triangles and squares) and is based on strokes of
near-even weight, which are low in contrast. This is most visible in the almost perfectly round stroke of
the o, which is nonetheless slightly ovoid.
The lowercase has tall ascenders, which rise above the cap line. The uppercase
characters present proportions similar to those of classical Roman capitals.

TYPOGRAPHIC CONSIDERATIONS
No Strike though
No Horizontal Scaling
No Drop Shadows
No Effects
Never use less than 120% Leading

OUR CORPORATE COLOURS
BRAND GUIDELINES
We were thinking that our primary colour palette consists of the Acid Green (Pantone 382) and Process Black.

We work closely with tquarly Ltd and would like to include their name on the card somewhere. I have attached images of the other brands that we work with as an idea or the small icons I have included that illustrate what we do?. I have very kindly been given permission to use any of the images off the files that I have included below, so I hope these help. I will include these below. I would be open to suggestions if it made the card more striking Can you do it?
Updates

Hi All, Just wanted to add a few thoughts but you are the guys with the creative visions (thats why are here) We are based in Wales, UK and we would be open to lots of different ideas on a theme but must be eye catching, Bold and FUN. If you can or think that the Welsh or any dragon could be put in there then go for it (its not a must have) We have also added some ideas for colour but again its over to you!! GO FOR IT ! Thanks and look forward to your visions! Owen

Hi All, Just thought I would sen through the contact details that need to be on the card. (if you want to play around with icons instead of the wording twitter, Facebook, go for it): Corvane Motion Limited Owen Pritchard Managing Director Mob: +44 (0)7582 913 406 e-mail: sales@corvanemotion.co.uk Web: Corvanemotion.co.uk twitter: @motionLetterbin Facebook: Corvane Motion Limited

```html
<!DOCTYPE html>
<html lang="en">
<head>
<meta charset="utf-8">
<title>Corvane Motion Limited – Business Card</title>
<link href="https://fonts.googleapis.com/css2?family=Lato:wght@400;700&display=swap" rel="stylesheet">
<style>
  :root {
    --backdrop-light: #b4b4b4;
    --backdrop-dark: #999999;
    --card-black: #1c1c1c;
    --card-black-soft: #2a2a2a;
    --card-white: #f1f1f3;
    --acid-green: #84c331;
    --mark-navy: #22408f;
    --ink-dark: #222222;
    --ink-light: #ffffff;
    --divider: #6a6a6a;
  }
  html, body {
    margin: 0;
    padding: 0;
    width: 1200px;
    height: 391px;
    overflow: hidden;
    background: var(--backdrop-dark);
  }
  .presentation {
    display: block;
    width: 1200px;
    height: 391px;
    font-family: "Lato", Arial, sans-serif;
  }
  .card-base { fill: url(#textureTone); }
  .card-white { fill: var(--card-white); }
  .green-band { fill: var(--acid-green); }
  .brand-dot { fill: var(--mark-navy); }
  .icon-line { fill: none; stroke: var(--ink-light); stroke-width: 1.6; }
  .icon-fill { fill: var(--ink-light); }
  .contact-divider { stroke: var(--divider); stroke-width: 1; }
  .holder-name { fill: var(--ink-light); font-weight: 700; font-size: 17px; }
  .holder-role { fill: var(--acid-green); font-weight: 400; font-size: 14px; }
  .contact-line { fill: var(--ink-light); font-weight: 400; font-size: 13.5px; }
  .brand-name-front { fill: var(--ink-dark); font-weight: 400; font-size: 17px; letter-spacing: 0.3px; }
  .brand-name-back { fill: var(--ink-light); font-weight: 400; font-size: 18px; letter-spacing: 0.6px; }
</style>
</head>
<body>
<svg class="presentation" viewBox="0 0 1144 373" xmlns="http://www.w3.org/2000/svg" aria-label="Corvane Motion Limited business card, front and back">
  <defs>
    <linearGradient id="backdropTone" x1="0" y1="0" x2="0" y2="1">
      <stop offset="0" stop-color="#b8b8b8"/>
      <stop offset="1" stop-color="#9c9c9c"/>
    </linearGradient>
    <radialGradient id="textureTone" cx="0.5" cy="0.45" r="0.75">
      <stop offset="0" stop-color="#2b2b2b"/>
      <stop offset="1" stop-color="#171717"/>
    </radialGradient>
  </defs>

  <rect class="backdrop" x="0" y="0" width="1144" height="373" fill="url(#backdropTone)"/>

  <!-- Front of card -->
  <g class="card card-front">
    <g role="img" aria-label="Dark woven carbon texture">
      <rect class="card-base" x="39" y="27" width="538" height="323"/>
    </g>
    <polygon class="card-white" points="39,27 260,27 322,188 268,350 39,350"/>
    <polygon class="green-band" points="260,27 285,27 352,207 330,207 322,188"/>
    <polygon class="green-band" points="313,216 352,216 346,258 299,258"/>
    <polygon class="green-band" points="296,265 344,265 334,310 281,310"/>

    <g class="icon icon-phone">
      <path class="icon-fill" d="M314,234 q8,-5 16,0 l0,3 l-4,0 l0,-2 q-4,-1.5 -8,0 l0,2 l-4,0 z"/>
      <rect class="icon-fill" x="316" y="238" width="12" height="7" rx="1"/>
    </g>
    <g class="icon icon-web">
      <rect class="icon-line" x="300" y="281" width="17" height="12" rx="1"/>
      <line class="icon-line" x1="308.5" y1="293" x2="308.5" y2="297"/>
      <line class="icon-line" x1="303" y1="297" x2="314" y2="297"/>
    </g>

    <g class="brand-lockup-front">
      <circle class="brand-dot" cx="113" cy="178" r="30"/>
      <text class="brand-name-front" x="150" y="166">CORVANE</text>
      <text class="brand-name-front" x="150" y="186">MOTION</text>
      <text class="brand-name-front" x="150" y="206">LIMITED</text>
    </g>

    <g class="holder">
      <text class="holder-name" x="526" y="100" text-anchor="end">Owen Pritchard</text>
      <text class="holder-role" x="526" y="117" text-anchor="end">Managing Director</text>
    </g>

    <g class="contact">
      <text class="contact-line" x="532" y="237" text-anchor="end">+44 (0)7582 913 406</text>
      <text class="contact-line" x="532" y="254" text-anchor="end">000 . 9876 . 5432</text>
      <line class="contact-divider" x1="340" y1="264.5" x2="532" y2="264.5"/>
      <text class="contact-line" x="532" y="285" text-anchor="end">sales@corvanemotion.co.uk</text>
      <text class="contact-line" x="532" y="302" text-anchor="end">Corvanemotion.co.uk</text>
    </g>
  </g>

  <!-- Back of card -->
  <g class="card card-back">
    <g role="img" aria-label="Dark woven carbon texture">
      <rect class="card-base" x="590" y="27" width="523" height="323"/>
    </g>
    <g class="brand-lockup-back">
      <circle class="brand-dot" cx="850" cy="137" r="68"/>
      <text class="brand-name-back" x="852" y="290" text-anchor="middle">CORVANE MOTION LIMITED</text>
    </g>
  </g>
</svg>
</body>
</html>
```